Vitamin B12 Liquid Drops Label

hi, i need a label designed for my vitamin b12 drops that i am going to be selling on shopzello. the label needs to quickly capture the attention of a buyer as he or she is scrolling through the thumbnail search results on shopzello.com my brand is called nralo. i already have an example brand logo i will be using, however, i need help designing the rest of the label. attached are some examples of labels i like for other supplements.some of these examples are pink. i do not want pink. please go for a blue/green color scheme. THE DESIGN MUST BE BOLD

Target Market(s)

adults ages 30 - 64

Font styles to use
Sans Serif

Colors
0455a3
cedeed
3176b5
85acd3
cfdeed
9bcb3b
abd037
cadf82
00a990

Requirements
Must have
• - bold design
• - somewhat gender-neutral color scheme because this will be used equally by men and women
• - B12 MUST be very prominent and visible on the label
Should not have
• - it should not be "crunchy" looking

```html
<!DOCTYPE html>
<html lang="en">
<head>
<meta charset="UTF-8">
<title>Nralo Vitamin B12 Label</title>
<link rel="stylesheet" href="https://fonts.googleapis.com/css2?family=Jost:wght@400;600;700;800&display=swap">
<style>
  :root {
    --canvas-bg: #f2f2f2;
    --label-white: #ffffff;
    --label-tint: #dcebf6;
    --brand-blue: #2f6fc4;
    --deep-blue: #0455a3;
    --mid-blue: #3176b5;
    --soft-blue: #85acd3;
    --pale-blue: #cedeed;
    --silver: #a7adb4;
    --ink: #111418;
  }
  html, body {
    margin: 0;
    padding: 0;
    width: 1200px;
    height: 900px;
    overflow: hidden;
    background: var(--canvas-bg);
    font-family: "Jost", sans-serif;
  }
  .canvas {
    position: relative;
    width: 1200px;
    height: 900px;
  }
  .label {
    position: absolute;
    left: 290px;
    top: 60px;
    width: 620px;
    height: 780px;
    overflow: hidden;
    background: linear-gradient(100deg, var(--label-white) 0%, #f3f8fc 45%, var(--label-tint) 100%);
    box-shadow: 0 2px 10px rgba(0, 0, 0, 0.08);
  }
  .label-swoosh {
    position: absolute;
    left: 0;
    top: 0;
    width: 620px;
    height: 780px;
  }
  .band-text {
    font-family: "Jost", sans-serif;
    font-weight: 400;
    font-size: 37px;
    fill: var(--label-white);
    letter-spacing: 0.5px;
  }
  .brand-name {
    position: absolute;
    left: 50px;
    top: 36px;
    height: 644px;
    writing-mode: vertical-rl;
    transform: rotate(180deg);
    font-weight: 800;
    font-size: 182px;
    line-height: 1;
    letter-spacing: -4px;
    text-align: center;
    color: var(--brand-blue);
    margin: 0;
  }
  .drop-art {
    position: absolute;
    left: 262px;
    top: 46px;
    width: 205px;
    height: 320px;
    border-radius: 12px;
    background: linear-gradient(180deg, var(--pale-blue) 0%, var(--soft-blue) 100%);
  }
  .product-title {
    margin: 0;
    color: var(--ink);
  }
  .product-title .vitamin {
    position: absolute;
    left: 253px;
    top: 388px;
    font-weight: 400;
    font-size: 62px;
    line-height: 1;
    letter-spacing: 0;
  }
  .product-title .b12 {
    position: absolute;
    left: 250px;
    top: 448px;
    font-weight: 700;
    font-size: 142px;
    line-height: 1;
    letter-spacing: -4px;
  }
  .net-volume {
    position: absolute;
    left: 256px;
    top: 582px;
    margin: 0;
    font-weight: 600;
    font-size: 38px;
    line-height: 1;
    color: var(--ink);
  }
</style>
</head>
<body>
<main class="canvas">
  <section class="label">
    <svg class="label-swoosh" viewBox="0 0 620 780" aria-hidden="true">
      <defs>
        <linearGradient id="swoosh-light" x1="0" y1="0" x2="1" y2="0">
          <stop offset="0" stop-color="#ffffff" stop-opacity="0"/>
          <stop offset="0.5" stop-color="#85acd3" stop-opacity="0.6"/>
          <stop offset="1" stop-color="#3176b5"/>
        </linearGradient>
        <linearGradient id="band-fill" x1="0" y1="0" x2="1" y2="0">
          <stop offset="0" stop-color="#1a5fc0"/>
          <stop offset="1" stop-color="#0455a3"/>
        </linearGradient>
      </defs>
      <path d="M0,690 C220,690 430,610 620,470 L620,580 C430,665 220,705 0,712 Z" fill="url(#swoosh-light)"/>
      <path d="M0,712 C230,706 440,650 620,575" fill="none" stroke="var(--silver)" stroke-width="9"/>
      <path d="M0,722 C230,716 440,664 620,594 L620,780 L0,780 Z" fill="url(#band-fill)"/>
      <text class="band-text" x="318" y="760" text-anchor="middle" transform="rotate(-2.5 318 760)">LIQUID DIETARY SUPPLEMENT</text>
    </svg>

    <h2 class="brand-name">NRALO</h2>

    <div class="drop-art" role="img" aria-label="Glossy blue water droplet illustration"></div>

    <h1 class="product-title">
      <span class="vitamin">VITAMIN</span>
      <span class="b12">B12</span>
    </h1>
    <p class="net-volume">2fl oz (60ml)</p>
  </section>
</main>
</body>
</html>
```